Varnel Corporate Website for technological company

We need a modern website to promote our product and services.
You can found the actually website at the address: www.varnel-example.ch

We are a new company for B2B market. We would like do show our high precision and innovation capability.

we need a section were is possible to easily upload "news" and documents for our customers.

Target Market(s)

B2B services in the industry market

Industry/Entity Type

It Company

Coding

Coded - Design and coding required

Number of Pages Required

5+ page

Font styles to use
Other font styles liked:
• We accept propositions

Requirements
Must have
• Easy to maintain
• Presentation of the Varnel company
• Presentation of Varnel services and products
• The customer can download our ducumentation
Nice to have
• Sexy and modern

```html
<!DOCTYPE html>
<html lang="en">
<head>
<meta charset="utf-8">
<title>Varnel Control Systems</title>
<link href="https://fonts.googleapis.com/css2?family=Open+Sans:wght@400;600;700&family=Play:wght@400;700&display=swap" rel="stylesheet">
<style>
:root{
  --gold:#aa9c5c;
  --gold-light:#b8ab6e;
  --ink:#333333;
  --text:#555555;
  --dark:#3a3a3a;
  --darker:#2e2e2e;
  --black:#111111;
  --panel:#f1f1f1;
  --line:#dddddd;
  --white:#ffffff;
}
*{box-sizing:border-box;margin:0;padding:0}
html,body{width:1200px;height:2416px;overflow:hidden}
body{font-family:"Open Sans",Arial,sans-serif;color:var(--text);background:var(--white);position:relative}
.heading{font-family:"Play",Arial,sans-serif}
.btn{display:inline-block;background:var(--gold);color:var(--white);font-family:"Play",Arial,sans-serif;font-weight:700;font-size:16px;letter-spacing:.5px;padding:0 30px;height:46px;line-height:46px;text-transform:uppercase}

/* top bar */
.topbar{position:absolute;top:0;left:677px;width:443px;height:44px;background:var(--dark);clip-path:polygon(0 0,100% 0,97% 100%,3% 100%);display:flex;align-items:center;justify-content:center;gap:30px;color:var(--white);font-size:12px;font-family:"Play",Arial,sans-serif}
.topbar .phone{color:var(--gold-light)}
.topbar .flag{display:inline-block;width:20px;height:13px;background:#4a5a9a;vertical-align:middle;margin-right:6px}

/* header */
.site-header{position:absolute;top:44px;left:0;width:1200px;height:85px}
.brand{position:absolute;left:74px;top:10px;display:flex;align-items:center;gap:12px}
.brand-square{width:44px;height:44px;background:var(--gold)}
.brand-name{font-family:"Play",Arial,sans-serif;font-weight:700;font-size:44px;color:var(--black);letter-spacing:1px}
.brand-suffix{font-family:"Play",Arial,sans-serif;font-weight:700;font-size:20px;color:var(--black);margin-top:14px}
.main-nav{position:absolute;right:74px;top:40px;display:flex;gap:4px}
.main-nav a{font-family:"Play",Arial,sans-serif;font-size:15px;color:var(--ink);text-decoration:none;padding:0 19px;height:36px;line-height:36px;text-transform:uppercase}
.main-nav a.active{background:var(--gold);color:var(--white)}

/* hero */
.hero{position:absolute;top:129px;left:0;width:1200px;height:470px;background:linear-gradient(180deg,#8f8f8d 0%,#b9b8b4 55%,#c9c8c4 100%)}
.hero-caption{position:absolute;top:135px;left:0;width:100%;text-align:center;color:var(--white)}
.hero-caption h1{font-family:"Play",Arial,sans-serif;font-size:50px;font-weight:400;letter-spacing:1px}
.hero-caption p{font-family:"Play",Arial,sans-serif;font-weight:700;font-size:19px;line-height:26px;width:860px;margin:4px auto 24px}
.hero-dots{position:absolute;top:431px;left:0;width:100%;display:flex;justify-content:center;gap:7px}
.hero-dots span{width:11px;height:11px;border-radius:50%;background:var(--black)}
.hero-dots span.on{background:var(--white)}

/* welcome */
.welcome{position:absolute;top:599px;left:74px;width:640px}
.welcome h2{font-family:"Play",Arial,sans-serif;font-size:27px;color:var(--ink);font-weight:400;margin-top:48px;margin-bottom:22px}
.welcome p{font-size:15px;line-height:26px;margin-bottom:11px}
.welcome .areas-title{color:var(--gold);font-weight:700;margin-top:16px;margin-bottom:6px}
.areas{list-style:none;margin-bottom:30px}
.areas li{font-size:15px;line-height:31px;display:flex;align-items:center;gap:12px}
.tick{width:14px;height:14px;border-radius:50%;background:var(--gold);display:inline-flex;align-items:center;justify-content:center}

.sidebar{position:absolute;top:653px;left:794px;width:332px}
.download{background:linear-gradient(180deg,#4a4a4a,#2e2e2e);height:66px;display:flex;align-items:center;gap:22px;padding-left:26px;color:var(--white);font-family:"Play",Arial,sans-serif;font-size:21px;line-height:24px;text-transform:uppercase}
.download small{font-size:14px}
.news{background:var(--panel);margin-top:14px;padding:22px 26px 32px}
.news h3{font-family:"Play",Arial,sans-serif;font-size:29px;font-weight:400;color:var(--ink);margin-bottom:18px}
.news-item{padding-bottom:16px;margin-bottom:18px;border-bottom:1px solid var(--line)}
.news-item:last-of-type{border-bottom:none;margin-bottom:12px}
.news-date{font-family:"Play",Arial,sans-serif;font-weight:700;color:var(--gold);font-size:15px;margin-bottom:10px}
.news-item p{font-size:15px;line-height:24px}

/* services */
.services{position:absolute;top:1194px;left:0;width:1200px;height:486px;background:var(--darker);text-align:center;color:var(--white)}
.services h2{font-family:"Play",Arial,sans-serif;font-size:29px;font-weight:400;margin-top:48px}
.service-grid{display:flex;justify-content:space-between;width:1066px;margin:30px auto 0}
.service{width:250px}
.service svg{height:76px}
.service h4{font-family:"Play",Arial,sans-serif;font-size:20px;color:var(--gold-light);font-weight:400;margin:14px 0 8px;text-transform:uppercase}
.service p{font-size:14px;line-height:23px;color:#e4e4e4}
.services .btn{margin-top:62px;padding:0 31px}

/* products */
.products{position:absolute;top:1680px;left:74px;width:1052px}
.products h2{font-family:"Play",Arial,sans-serif;font-size:27px;font-weight:400;color:var(--ink);margin-top:36px}
.product-tabs{position:absolute;top:96px;left:0;width:180px;z-index:2}
.product-tabs div{height:48px;line-height:48px;padding-left:29px;font-family:"Play",Arial,sans-serif;font-weight:700;font-size:14px;text-transform:uppercase;color:var(--ink);background:var(--panel);border:1px solid var(--line);margin-bottom:5px}
.product-tabs div.active{background:var(--gold);color:var(--white);border-color:var(--gold)}
.product-panel{position:absolute;top:96px;left:180px;width:872px;height:330px;background:var(--panel);border:1px solid var(--line)}
.product-mark{position:absolute;left:24px;top:36px;width:140px;height:40px;background:linear-gradient(90deg,#d8d8d8,#bdbdbd)}
.product-title{position:absolute;left:176px;top:30px}
.product-title h3{font-family:"Play",Arial,sans-serif;font-size:22px;color:var(--gold);font-weight:700}
.product-title span{font-family:"Play",Arial,sans-serif;font-size:14px;font-weight:700;color:var(--ink);text-transform:uppercase}
.product-desc{position:absolute;left:24px;top:94px;width:500px;font-size:15px;line-height:26px}
.product-panel .btn{position:absolute;left:24px;top:248px}
.product-photo{position:absolute;right:24px;top:36px;width:310px;height:260px;border:1px solid var(--line);background:var(--white);padding:8px}
.product-photo div{width:100%;height:100%;background:radial-gradient(circle,#4f7a5a 0%,#3a5f46 45%,#eef0ee 75%)}

/* newsletter */
.newsletter{position:absolute;top:2151px;left:0;width:1200px;height:93px;background:var(--dark);display:flex;align-items:center;padding:0 74px;color:var(--white);font-family:"Play",Arial,sans-serif;font-weight:700;font-size:17px}
.newsletter .label{display:flex;align-items:center;gap:14px;width:236px;text-transform:uppercase}
.newsletter .field{width:333px;height:44px;background:var(--white);color:#777;font-family:"Open Sans",Arial,sans-serif;font-weight:400;font-size:14px;padding-left:15px;line-height:44px}
.newsletter .btn{height:44px;line-height:44px;padding:0 15px;margin-left:7px;font-size:15px}
.follow{margin-left:auto;display:flex;align-items:center;gap:19px;text-transform:uppercase}
.follow i{display:inline-block;width:22px;height:22px;background:#d8d8d8;border-radius:3px}

/* footer */
.site-footer{position:absolute;top:2244px;left:0;width:1200px;height:172px;background:var(--black);text-align:center;color:#aaaaaa}
.footer-nav{display:flex;justify-content:center;gap:48px;margin-top:50px}
.footer-nav a{font-family:"Play",Arial,sans-serif;font-size:15px;color:#dddddd;text-decoration:none;text-transform:uppercase}
.site-footer p{font-size:13px;margin-top:28px}
.site-footer p + p{margin-top:8px}
</style>
</head>
<body>

<div class="topbar">
  <span class="phone">&#9990; +41 (0)21 555 01 23</span>
  <span>&#9679; MEMBER LOG IN &#709;</span>
  <span><i class="flag"></i>EN &#709;</span>
</div>

<header class="site-header">
  <div class="brand">
    <span class="brand-square"></span>
    <span class="brand-name">VARNEL</span>
    <span class="brand-suffix">Sagl</span>
  </div>
  <nav class="main-nav">
    <a class="active">Home</a><a>Services</a><a>Products</a><a>Examples</a><a>Download</a><a>Contacts</a>
  </nav>
</header>

<section class="hero" role="img" aria-label="Photo of a compact electronic control board with cable on a grey surface">
  <div class="hero-caption">
    <h1>VARNEL CONTROL SYSTEMS</h1>
    <p>VARNEL Ltd. designs systems in which electronics, software and mechanics are perfectly integrated to achieve uncompromising performance.</p>
    <span class="btn">View products</span>
  </div>
  <div class="hero-dots"><span class="on"></span><span></span><span></span><span></span></div>
</section>

<section class="welcome">
  <h2>WELCOME TO OUR WEBSITE</h2>
  <p>The ever-increasing complexity in modern systems, the search for reliability and performance and the continuous desire to reduce production costs and dimensions of the products require a rigorous integration between the electronic units, software and mechanical systems.</p>
  <p>VARNEL Ltd. designs systems in which electronics, software and mechanics are perfectly integrated to achieve uncompromising performance.</p>
  <p>VARNEL Ltd. designs systems in which electronics, software and mechanics are perfectly integrated to achieve uncompromising performance.</p>
  <p class="areas-title">VARNEL Ltd. is a company active in the following areas:</p>
  <ul class="areas">
    <li><span class="tick"><svg width="8" height="8" viewBox="0 0 8 8"><path d="M1 4l2 2 4-4" stroke="#fff" stroke-width="1.6" fill="none"/></svg></span>Simulation and modeling of complete processes</li>
    <li><span class="tick"><svg width="8" height="8" viewBox="0 0 8 8"><path d="M1 4l2 2 4-4" stroke="#fff" stroke-width="1.6" fill="none"/></svg></span>Concept and design of electronic circuits and mechanical units</li>
    <li><span class="tick"><svg width="8" height="8" viewBox="0 0 8 8"><path d="M1 4l2 2 4-4" stroke="#fff" stroke-width="1.6" fill="none"/></svg></span>Development of application specific control software</li>
    <li><span class="tick"><svg width="8" height="8" viewBox="0 0 8 8"><path d="M1 4l2 2 4-4" stroke="#fff" stroke-width="1.6" fill="none"/></svg></span>Rapid prototyping (electronic cards, mechanisms ...)</li>
  </ul>
  <span class="btn">Read more</span>
</section>

<aside class="sidebar">
  <div class="download">
    <svg width="32" height="32" viewBox="0 0 32 32"><path d="M16 3v15M10 12l6 6 6-6" stroke="#c9bb7a" stroke-width="4" fill="none"/><rect x="3" y="22" width="26" height="7" fill="#c9bb7a"/></svg>
    <span>Downlaod<br>brochure Varnel <small>(EN)</small></span>
  </div>
  <div class="news">
    <h3>LATEST NEWS</h3>
    <div class="news-item">
      <div class="news-date">OCT 16, 2016</div>
      <p>The Varnel team will be present at the stand A16 of Techforma exhibition in Bern, between 6 and 8 september 2016.</p>
    </div>
    <div class="news-item">
      <div class="news-date">OCT 16, 2016</div>
      <p>Added the 'application' page, showing some of the developments of Varnel Ltd...</p>
    </div>
    <span class="btn">Read all news</span>
  </div>
</aside>

<section class="services">
  <h2>OUR SERVICES</h2>
  <div class="service-grid">
    <div class="service">
      <svg viewBox="0 0 76 76" width="76"><rect x="18" y="18" width="40" height="40" fill="none" stroke="#fff" stroke-width="4"/><rect x="28" y="28" width="20" height="20" fill="#fff"/><path d="M26 6v10M34 6v10M42 6v10M50 6v10M26 60v10M34 60v10M42 60v10M50 60v10M6 26h10M6 34h10M6 42h10M6 50h10M60 26h10M60 34h10M60 42h10M60 50h10" stroke="#fff" stroke-width="3"/></svg>
      <h4>Electronics</h4>
      <p>VARNEL Sàrl being active in all fields associated with actuator electronics, can develop solutions integrating...</p>
    </div>
    <div class="service">
      <svg viewBox="0 0 76 76" width="76"><path d="M12 64L50 26M26 12l38 38" stroke="#fff" stroke-width="9" stroke-linecap="round"/><circle cx="54" cy="20" r="12" fill="none" stroke="#fff" stroke-width="6"/><circle cx="18" cy="18" r="8" fill="#fff"/></svg>
      <h4>Mechanics</h4>
      <p>VARNEL Sàrl being active in all fields associated with actuator electronics, can develop solutions integrating...</p>
    </div>
    <div class="service">
      <svg viewBox="0 0 76 76" width="76"><rect x="24" y="6" width="46" height="54" fill="#fff"/><circle cx="40" cy="34" r="11" fill="#2e2e2e"/><circle cx="22" cy="52" r="16" fill="#fff" stroke="#2e2e2e" stroke-width="3"/><circle cx="22" cy="52" r="5" fill="#2e2e2e"/></svg>
      <h4>Software</h4>
      <p>VARNEL Sàrl being active in all fields associated with actuator electronics, can develop solutions integrating...</p>
    </div>
    <div class="service">
      <svg viewBox="0 0 110 76" width="110"><rect x="14" y="6" width="82" height="54" rx="3" fill="none" stroke="#fff" stroke-width="4"/><path d="M4 66h102" stroke="#fff" stroke-width="6"/><path d="M55 20l12 6v13l-12 6-12-6V26z" fill="none" stroke="#fff" stroke-width="3"/></svg>
      <h4>Simulation &amp; Modeling</h4>
      <p>VARNEL Sàrl being active in all fields associated with actuator electronics, can develop solutions integrating...</p>
    </div>
  </div>
  <span class="btn">View all services</span>
</section>

<section class="products">
  <h2>OUR PRODUCTS</h2>
  <div class="product-tabs">
    <div>Motor driver</div>
    <div class="active">Bus interface</div>
  </div>
  <div class="product-panel">
    <div class="product-mark" role="img" aria-label="Small product emblem illustration"></div>
    <div class="product-title">
      <h3>KESTRELON:</h3>
      <span>Intelligent control for electric motors</span>
    </div>
    <p class="product-desc">Kestrelon is an electronics board developed for the control of DC and BLDC motors with a power ranging from 1W to 250W. This board integrates a powerful ARM processor, a power stage, two communication buses, a number of interfaces compatible with the different position sensor standards available on the market...</p>
    <span class="btn">View all product</span>
    <div class="product-photo"><div role="img" aria-label="Photo of the green motor control circuit board with terminal connectors"></div></div>
  </div>
</section>

<section class="newsletter">
  <div class="label">
    <svg width="18" height="14" viewBox="0 0 18 14"><rect width="18" height="14" fill="#aa9c5c"/><path d="M0 0l9 7 9-7" stroke="#3a3a3a" stroke-width="1.5" fill="none"/></svg>
    Newsletter sign up
  </div>
  <div class="field">Enter Email Address</div>
  <span class="btn">Sign up</span>
  <div class="follow">Follow us: <i></i><i></i><i></i><i></i><i></i></div>
</section>

<footer class="site-footer">
  <nav class="footer-nav"><a>Home</a><a>Services</a><a>Products</a><a>Examples</a><a>Download</a><a>Contacts</a></nav>
  <p>Copyright © 2016. Company Name. All Right Reserved</p>
  <p>Terms of Services &nbsp;|&nbsp; Privacy Policy</p>
</footer>

</body>
</html>
```